Trade Show Design

Two, doublesided backdrops/one doublesided banner/one countertop. I have 3 sample pictures of the 3 items that we are purchasing and all the dimensions are listed on the file names.
website: www.brickwisestudio.net
We are a training center that teaches homeowner's how to do their own home renovations through in-person classes with hands-on training.
We are looking to update our tradeshow displays utilizing stock photos as our photos do not have high enough resolution. I have attached lots of example pictures to select from but some of my favourites that I want to use are over 10 MB so they won't upload. Will have to figure out a different way to upload. Our tagline is Take on any job with skill. We also use words such as "learn to reno" or "practical, hands-on training". We want to use our current branding (pictures of our minivan are uploaded as well) and our color palette document and really show people what we are all about - classes that people can attend so they can learn to reno their home.
Updates

For the 2 backdrops, we would like them to either be stand-alone or together incase we go to a trade show and only have room for 1 of them. They are to be different designs, front and back but a continuous flow if we are to use them together. Again, I have to figure out how to upload additional pictures as some of the ones I want to use are larger. Thanks!

Same with the Banner that is also double-sided - this is to be a different design for the back and front. We want minimal wording on everything but we really want to showcase what we do so that people can figure it out quickly when they walk by our booth....we offer in-person class with hands-on training. Learn to do by doing. Like on our vehicle that I sent example pictures of, we can put a list of a few topics so that people can understand:
Renovation Topics:
Bathroom
Drywall
Flooring
Tiling
Basement
Framing
Plumbing
Baseboards
Feature Walls

Here is the link to the Vornel Box to additional photos.

https://files.vornelbox.net/shared/7QK4r_mz2-TX8LwBnPe5YuJsdA0fGhRkZ?view=open

Thanks,
Marla

```html
<!DOCTYPE html>
<html lang="en">
<head>
<meta charset="utf-8">
<title>Brickwise Studio — Trade Show Displays</title>
<link rel="stylesheet" href="https://fonts.googleapis.com/css2?family=Oswald:wght@500;600;700&family=Poppins:wght@400;500&display=swap">
<style>
  :root {
    --bg: #dfe5ec;
    --teal: #2b6a72;
    --teal-dark: #1d4a54;
    --orange: #d99a34;
    --cream: #e9ebc3;
    --sky: #b5d2ea;
    --ink: #1f3f48;
    --white: #f6f7f4;
    --blue: #4d7fb8;
  }
  * { box-sizing: border-box; margin: 0; padding: 0; }
  html, body { width: 1200px; height: 488px; overflow: hidden; background: var(--bg); }
  body { position: relative; font-family: "Poppins", sans-serif; color: var(--ink); }

  .display { position: absolute; overflow: hidden; box-shadow: 0 6px 14px rgba(30,50,70,.15); }
  .grid { display: grid; }

  .cell { display: flex; flex-direction: column; align-items: center; justify-content: center; text-align: center; padding: 4px; min-width: 0; }
  .cream { background: var(--cream); }
  .teal { background: var(--teal); color: var(--white); }
  .orange { background: var(--orange); color: var(--white); }
  .sky { background: var(--sky); color: var(--ink); }

  .photo { width: 100%; height: 100%; }
  .photo-warm { background: linear-gradient(135deg, #c98a3a, #e7b76a 60%, #f2e1c0); }
  .photo-mono { background: linear-gradient(160deg, #3f5f86, #8aa6c8 70%, #c7d6e8); }
  .photo-van { background: linear-gradient(120deg, #e8ecef 0%, #f6f6f4 45%, #2f6fa8 85%, var(--orange) 100%); }
  .photo-worker { background: linear-gradient(150deg, #5a4a3c, #9a8670 60%, #c9b89d); }
  .photo-ceiling { background: linear-gradient(160deg, #f1efea, #d9cfc4 55%, #b24a3e 100%); }
  .photo-couple { background: linear-gradient(135deg, #d7a23f, #edc56d 60%, #f4dc9b); }
  .photo-smile { background: linear-gradient(150deg, #c9b6a0, #8d6d58 60%, #3f4f66); }
  .photo-drill { background: linear-gradient(160deg, #ece8e0, #3f73a8 55%, #c7533f 100%); }

  .topics { font-family: "Oswald", sans-serif; font-weight: 500; font-size: 8px; line-height: 1.45; letter-spacing: .02em; text-transform: uppercase; }
  .icon { width: 22px; height: 22px; margin-bottom: 6px; }

  .brand { display: flex; flex-direction: column; align-items: center; gap: 3px; }
  .brand-row { display: flex; align-items: center; gap: 4px; white-space: nowrap; }
  .brand-mark { width: 9px; height: 9px; background: var(--orange); flex: none; }
  .brand-name { font-family: "Oswald", sans-serif; font-weight: 600; font-size: 9px; color: var(--teal); text-transform: uppercase; letter-spacing: .02em; white-space: nowrap; }
  .tagline { font-size: 5px; color: var(--teal); white-space: nowrap; }

  .headline { font-family: "Oswald", sans-serif; font-weight: 700; line-height: .98; letter-spacing: -.01em; }
  .underline { display: block; margin: 5px auto 0; }

  /* backdrop one */
  .backdrop-one { left: 50px; top: 84px; width: 320px; height: 320px;
    grid-template-columns: 74px 82px 86px 78px; grid-template-rows: 104px 108px 108px; }
  .backdrop-one .learn { grid-column: 2 / 4; }
  .backdrop-one .learn .headline { font-size: 38px; }
  .backdrop-one .van { grid-column: 1 / 4; }
  .backdrop-one .brand-name { font-size: 8px; }
  .backdrop-one .tagline { font-size: 4.3px; }

  /* backdrop two */
  .backdrop-two { left: 390px; top: 84px; width: 320px; height: 320px;
    grid-template-columns: 122px 100px 98px; grid-template-rows: 110px 110px 100px; }
  .backdrop-two .intro { grid-row: 1 / 4; justify-content: space-between; padding: 30px 8px 20px; }
  .backdrop-two .scene-wide { grid-column: 2 / 4; }
  .practical { font-size: 23px; color: var(--teal); }
  .practical .pill { display: inline-block; white-space: nowrap; background: var(--orange); color: var(--white); padding: 2px 5px; border-radius: 3px; margin: 3px 0; }
  .web-pill { display: flex; align-items: center; gap: 5px; background: var(--teal); color: var(--white); font-size: 6.5px; padding: 3px 8px 3px 3px; border-radius: 10px; white-space: nowrap; }
  .web-dot { width: 11px; height: 11px; border-radius: 50%; background: #f0c23a; }

  /* counter */
  .counter { left: 735px; top: 262px; width: 110px; height: 178px; background: var(--teal-dark); border-radius: 12px 12px 6px 6px;
    display: flex; flex-direction: column; align-items: center; padding-top: 68px; color: var(--white); }
  .counter .brand-name { color: var(--white); font-size: 8px; }
  .counter .tagline { color: #cfdde0; font-size: 4.5px; }
  .counter .headline { font-size: 14px; margin-top: 10px; font-weight: 600; }

  /* banner one */
  .banner-offer { left: 870px; top: 64px; width: 110px; height: 380px; background: var(--white);
    display: flex; flex-direction: column; align-items: center; padding-top: 26px; }
  .banner-offer .brand-name { font-size: 8px; }
  .banner-offer .tagline { font-size: 4.5px; }
  .offer { margin-top: 16px; text-align: center; font-family: "Oswald", sans-serif; font-weight: 700; }
  .offer-we { color: var(--orange); font-size: 11px; }
  .offer-box { display: inline-block; background: var(--ink); color: var(--cream); font-size: 14px; padding: 0 5px; margin: 1px 0; }
  .offer-class { color: var(--blue); font-size: 14px; }
  .offer-hands { color: var(--ink); font-size: 10px; }
  .banner-offer .topics { font-size: 5px; color: var(--ink); text-align: center; }
  .banner-offer .topic-group { display: flex; flex-direction: column; align-items: center; margin-top: 9px; }
  .banner-offer .topic-group.accent .topics { color: var(--orange); }
  .banner-offer .icon { width: 13px; height: 13px; margin-bottom: 3px; }
  .banner-offer .photo { height: 96px; margin-top: auto; }

  /* banner two */
  .banner-learn { left: 1005px; top: 52px; width: 120px; height: 404px; background: var(--white);
    display: flex; flex-direction: column; align-items: center; }
  .banner-learn .photo-drill { height: 178px; flex: none; }
  .banner-learn .brand { margin-top: 20px; }
  .banner-learn .brand-name { font-size: 8px; }
  .banner-learn .tagline { font-size: 4.5px; }
  .banner-learn .headline { margin-top: 14px; font-size: 22px; text-align: right; align-self: stretch; padding-right: 12px; color: var(--ink); }
  .banner-learn .headline .to { color: var(--blue); }
  .banner-learn .headline .reno { color: var(--orange); }
  .banner-learn .photo-van { height: 86px; margin-top: auto; flex: none; }
</style>
</head>
<body>

<!-- Backdrop one: Learn To Reno -->
<section class="display grid backdrop-one">
  <div class="photo photo-warm" role="img" aria-label="Woman in safety glasses smoothing a wall"></div>
  <div class="cell cream">
    <div class="brand">
      <div class="brand-row"><span class="brand-mark"></span><span class="brand-name">Brickwise Studio</span></div>
      <span class="tagline">Take on any job with skill.</span>
    </div>
  </div>
  <div class="photo photo-mono" role="img" aria-label="Woman sanding a wood surface, blue tone"></div>
  <div class="cell orange">
    <svg class="icon" viewBox="0 0 24 24" fill="none" stroke="#fff" stroke-width="1.6"><path d="M4 7h11v12a2 2 0 0 1-2 2H6a2 2 0 0 1-2-2z"/><path d="M18 4v9M16 13h4v3h-4z"/></svg>
    <p class="topics">Drywall<br>Feature Walls<br>Framing</p>
  </div>

  <div class="cell cream">
    <svg class="icon" viewBox="0 0 24 24" fill="none" stroke="#1f3f48" stroke-width="1.6"><rect x="4" y="7" width="16" height="13" rx="2"/><path d="M9 7V4h6v3M9 11l6 6M15 11l-6 6"/></svg>
    <p class="topics">Tiling<br>Bathroom<br>Plumbing</p>
  </div>
  <div class="cell teal learn">
    <h2 class="headline">Learn<br>To Reno</h2>
    <svg class="underline" width="70" height="8" viewBox="0 0 70 8"><path d="M2 6c20-3 45-4 66-4" stroke="#d99a34" stroke-width="1.5" fill="none"/></svg>
  </div>
  <div class="cell sky">
    <svg class="icon" viewBox="0 0 24 24" fill="none" stroke="#1f3f48" stroke-width="1.6"><path d="M4 4l16 16M20 4L4 20M3 3h4v4M17 17h4v4"/></svg>
    <p class="topics">Flooring<br>Baseboards<br>Basement</p>
  </div>

  <div class="photo photo-van van" role="img" aria-label="Branded company minivan on orange"></div>
  <div class="photo photo-worker" role="img" aria-label="Man in safety glasses working on a wall"></div>
</section>

<!-- Backdrop two: Practical, Hands-on Training -->
<section class="display grid backdrop-two">
  <div class="cell cream intro">
    <div class="brand">
      <div class="brand-row"><span class="brand-mark"></span><span class="brand-name">Brickwise Studio</span></div>
      <span class="tagline">Take on any job with skill.</span>
    </div>
    <h2 class="headline practical">Practical,<br><span class="pill">Hands-on</span><br>Training.</h2>
    <div class="web-pill"><span class="web-dot"></span>brickwisestudio.net</div>
  </div>
  <div class="cell teal">
    <svg class="icon" viewBox="0 0 24 24" fill="none" stroke="#fff" stroke-width="1.6"><path d="M4 7h11v12a2 2 0 0 1-2 2H6a2 2 0 0 1-2-2z"/><path d="M18 4v9M16 13h4v3h-4z"/></svg>
    <p class="topics">Drywall<br>Feature Walls<br>Framing</p>
  </div>
  <div class="cell cream">
    <svg class="icon" viewBox="0 0 24 24" fill="none" stroke="#2b6a72" stroke-width="1.6"><path d="M4 4l16 16M20 4L4 20M3 3h4v4M17 17h4v4"/></svg>
    <p class="topics">Flooring<br>Baseboards<br>Basement</p>
  </div>
  <div class="photo photo-ceiling scene-wide" role="img" aria-label="Couple installing a ceiling light fixture"></div>
  <div class="photo photo-couple" role="img" aria-label="Smiling couple holding tools on yellow"></div>
  <div class="cell sky">
    <svg class="icon" viewBox="0 0 24 24" fill="none" stroke="#1f3f48" stroke-width="1.6"><rect x="4" y="7" width="16" height="13" rx="2"/><path d="M9 7V4h6v3M9 11l6 6M15 11l-6 6"/></svg>
    <p class="topics">Tiling<br>Bathroom<br>Plumbing</p>
  </div>
</section>

<!-- Countertop -->
<section class="display counter">
  <div class="brand">
    <div class="brand-row"><span class="brand-mark"></span><span class="brand-name">Brickwise Studio</span></div>
    <span class="tagline">Take on any job with skill.</span>
  </div>
  <h2 class="headline">Learn To Reno</h2>
  <svg class="underline" width="50" height="6" viewBox="0 0 50 6"><path d="M2 4c15-2 30-3 46-3" stroke="#d99a34" stroke-width="1.2" fill="none"/></svg>
</section>

<!-- Banner front -->
<section class="display banner-offer">
  <div class="brand">
    <div class="brand-row"><span class="brand-mark"></span><span class="brand-name">Brickwise Studio</span></div>
    <span class="tagline">Take on any job with skill.</span>
  </div>
  <div class="offer">
    <div class="offer-we">We Offer</div>
    <div class="offer-box">IN-PERSON</div>
    <div class="offer-class">CLASS WITH</div>
    <div class="offer-hands">Hands-On Training</div>
  </div>
  <div class="topic-group">
    <svg class="icon" viewBox="0 0 24 24" fill="none" stroke="#1f3f48" stroke-width="1.6"><rect x="4" y="7" width="16" height="13" rx="2"/><path d="M9 7V4h6v3M9 11l6 6M15 11l-6 6"/></svg>
    <p class="topics">Tiling | Bathroom<br>Plumbing</p>
  </div>
  <div class="topic-group accent">
    <svg class="icon" viewBox="0 0 24 24" fill="none" stroke="#d99a34" stroke-width="1.6"><path d="M4 7h11v12a2 2 0 0 1-2 2H6a2 2 0 0 1-2-2z"/><path d="M18 4v9M16 13h4v3h-4z"/></svg>
    <p class="topics">Drywall | Framing<br>Feature Walls</p>
  </div>
  <div class="topic-group">
    <svg class="icon" viewBox="0 0 24 24" fill="none" stroke="#1f3f48" stroke-width="1.6"><path d="M4 4l16 16M20 4L4 20M3 3h4v4M17 17h4v4"/></svg>
    <p class="topics">Flooring | Basement<br>Baseboards</p>
  </div>
  <div class="photo photo-smile" role="img" aria-label="Smiling couple measuring a wall"></div>
</section>

<!-- Banner back -->
<section class="display banner-learn">
  <div class="photo photo-drill" role="img" aria-label="Woman using a power drill and a girl painting a wall"></div>
  <div class="brand">
    <div class="brand-row"><span class="brand-mark"></span><span class="brand-name">Brickwise Studio</span></div>
    <span class="tagline">Take on any job with skill.</span>
  </div>
  <h2 class="headline">Learn <span class="to">To</span><br><span class="reno">Reno</span></h2>
  <svg class="underline" width="60" height="6" viewBox="0 0 60 6"><path d="M2 4c18-2 36-3 56-3" stroke="#d99a34" stroke-width="1.2" fill="none"/></svg>
  <div class="photo photo-van" role="img" aria-label="Branded company minivan"></div>
</section>

</body>
</html>
```